NCBG website design

We need a page template website design for a cms website. Please see the brief attached for the details.
The client is the National Copperfleece Breeders Guild which is an organisation promoting the Copperfleece Sheep Breed within Australia.
Updates

Project Deadline Extended
Reason: So that my top few designs can make changes and re-submit.

Target Market(s)

See attached brief

```html
<!DOCTYPE html>
<html lang="en">
<head>
<meta charset="utf-8">
<title>National Copperfleece Breeders Guild</title>
<link rel="stylesheet" href="https://fonts.googleapis.com/css2?family=Ubuntu:wght@400;500;700&family=Roboto:wght@400;500;700&display=swap">
<style>
:root{
  --green:#0d9444;
  --green-dark:#0a7d39;
  --green-light:#14b052;
  --ink:#2b2b2b;
  --text:#444;
  --muted:#666;
  --page:#e9eff5;
  --header:#f3f3f3;
  --black:#111;
  --yellow:#fdd82a;
  --white:#fff;
}
*{box-sizing:border-box;margin:0;padding:0}
html,body{width:978px;height:1200px;overflow:hidden}
body{position:relative;background:var(--page);font-family:"Roboto",sans-serif;color:var(--text);font-size:10px}
.abs{position:absolute}
.site-header{left:0;top:0;width:978px;height:92px;background:var(--header)}
.brand{left:124px;top:8px;display:flex;align-items:center;gap:8px}
.brand-mark{width:64px;height:64px;border-radius:50%;background:var(--green)}
.brand-name{font-family:"Ubuntu",sans-serif;font-weight:700;font-size:21px;color:var(--green);line-height:1}
.utility{right:108px;top:13px;font-size:10px;color:var(--muted)}
.search-box{left:663px;top:59px;width:130px;height:22px;border:1px solid #c9c9c9;border-radius:3px;background:var(--white);font-size:10px;color:#777;padding:5px 9px}
.search-box svg{position:absolute;right:8px;top:4px}
.login-btn{left:802px;top:59px;width:68px;height:22px;border:1px solid #c9c9c9;border-radius:3px;background:#f0f0f0;font-size:10px;color:#555;text-align:center;line-height:20px}
.main-nav{left:0;top:92px;width:978px;height:30px;background:var(--green);border-bottom:3px solid #3cbf6a}
.main-nav ul{position:absolute;left:107px;top:0;display:flex;list-style:none;height:27px}
.main-nav li{font-family:"Ubuntu",sans-serif;font-size:12.5px;color:var(--white);line-height:29px;padding:0 21px;border-right:1px solid #3aaa63}
.main-nav li:last-child{border-right:0}
.main-nav li.active{background:#222;padding:0 16px}
.hero{left:0;top:122px;width:978px;height:348px;background:linear-gradient(180deg,#6c6f55 0%,#8f7a55 35%,#a8825a 65%,#6d4a2c 100%)}
.hero-arrow{top:172px}
.hero-caption{left:128px;top:278px;width:722px;height:68px;background:rgba(30,30,30,.55);font-family:"Ubuntu",sans-serif;font-weight:700;font-size:21.5px;color:var(--white);text-align:center;line-height:27px;padding-top:6px}
.side-panel{left:107px;top:472px;width:251px;height:338px;background:var(--white);box-shadow:0 2px 3px rgba(0,0,0,.15);border-radius:0 0 4px 4px}
.quick-btn{left:115px;width:237px;height:54px;background:linear-gradient(180deg,var(--green-light),var(--green));display:flex;align-items:center;border-bottom:1px solid #0a8a3e}
.quick-btn .ico{width:52px;height:38px;display:flex;align-items:center;justify-content:center;border-right:1px solid #4cc679}
.quick-btn span{font-family:"Ubuntu",sans-serif;font-weight:700;font-size:14px;color:var(--white);padding-left:12px}
.box-title{background:var(--black);color:var(--white);font-family:"Ubuntu",sans-serif;font-weight:500;font-size:13.5px;height:26px;line-height:26px}
.ads-title{left:115px;top:677px;width:237px;padding-left:10px}
.ads-title .arrows{position:absolute;right:8px;top:0}
.ad-slot{top:708px;width:115px;height:96px}
.welcome{left:386px;top:494px;width:484px}
.welcome h1{font-family:"Ubuntu",sans-serif;font-weight:500;font-size:19px;color:var(--ink)}
.welcome h1 em{font-style:normal;color:var(--green)}
.welcome p{font-size:9.9px;line-height:16px;margin-top:9px;color:#444;text-align:justify}
.read-more{right:108px;top:642px;font-weight:700;font-size:9.5px;color:#222}
.card{background:var(--white);box-shadow:0 1px 3px rgba(0,0,0,.2)}
.semen{left:386px;top:677px;width:229px;height:133px}
.semen .box-title,.calendar .box-title{text-align:center}
.semen h3{font-size:10.5px;font-weight:500;color:#555;text-align:center;line-height:14px;margin:5px 12px 0;padding-bottom:4px;border-bottom:1px solid #ddd}
.stud-list{display:grid;grid-template-columns:1fr 1fr;padding:5px 0 0 12px;list-style:none;row-gap:2px}
.stud-list li{font-size:10.5px;color:#555;display:flex;align-items:center;gap:6px;height:14px}
.calendar{left:642px;top:677px;width:229px;height:133px}
.cal-table{width:206px;margin:6px 0 0 11px;border-collapse:collapse;font-size:9.8px;color:#555}
.cal-table th{font-weight:500;text-align:left;vertical-align:top;line-height:13px;padding-bottom:4px;border-bottom:1px solid #ddd}
.cal-table td{line-height:15px}
.cal-table tr:nth-child(2) td{padding-top:5px}
.cal-more{right:14px;bottom:6px;font-size:9px;color:#555}
.newsletter{left:107px;top:835px;width:251px;height:92px;background:var(--yellow);border-radius:6px;border:2px solid #f2e800}
.newsletter h2,.gallery h2{font-family:"Ubuntu",sans-serif;font-weight:500;font-size:15.5px;color:#555}
.newsletter h2{position:absolute;left:13px;top:7px}
.newsletter .inner{position:absolute;left:6px;top:30px;width:235px;height:52px;background:var(--white);border-radius:6px}
.email-field{position:absolute;left:10px;top:13px;width:156px;height:26px;border:1px solid #ccc;border-right:0;border-radius:4px 0 0 4px;font-size:10px;color:#444;padding:7px 11px}
.subscribe{position:absolute;left:166px;top:13px;width:66px;height:26px;background:linear-gradient(180deg,#666,#444);border-radius:0 4px 4px 0;color:var(--white);font-weight:500;font-size:10.5px;text-align:center;line-height:26px}
.gallery{left:386px;top:835px;width:485px;height:93px;border-radius:4px}
.gallery h2{position:absolute;left:11px;top:7px}
.gallery .arrows,.sponsors .arrows{position:absolute}
.thumb{top:30px;width:100px;height:54px;border:1px solid #aaa;padding:2px;background:var(--white)}
.thumb div{width:100%;height:100%}
.sep{top:30px;width:0;height:54px;border-left:1px dotted #aaa}
.sponsors{left:107px;top:949px;width:764px;height:99px;background:var(--white)}
.sponsors h2{position:absolute;left:24px;top:12px;font-family:"Ubuntu",sans-serif;font-weight:500;font-size:13.5px;color:#555}
.sponsors .rule{position:absolute;left:24px;top:35px;width:705px;border-top:2px solid #999}
.sponsor{position:absolute;top:49px;height:34px;display:flex;align-items:center;font-family:"Roboto",sans-serif;font-weight:700;font-size:20px}
.sponsor-shadow{left:120px;top:1046px;width:740px;height:14px;border-radius:50%;background:radial-gradient(ellipse at center,rgba(120,130,180,.35),rgba(120,130,180,0) 70%)}
.site-footer{left:0;top:1076px;width:978px;height:124px;background:var(--white)}
.foot-tag{top:1077px;width:124px;height:20px;background:var(--green);color:var(--white);font-family:"Ubuntu",sans-serif;font-weight:500;font-size:12px;line-height:20px;padding-left:8px}
.foot-tag::after{content:"";position:absolute;left:22px;top:20px;border-left:10px solid var(--green);border-bottom:10px solid transparent}
.quick-links{top:1117px;list-style:none;font-size:9px;color:#555}
.quick-links li{height:14.5px;display:flex;align-items:center;gap:6px}
.map{left:299px;top:1095px;width:191px;height:90px;border:3px solid var(--green);background:linear-gradient(135deg,#e8ebe3,#d7dfcc 55%,#e9ece5)}
.contact-list{left:509px;top:1116px;font-size:9px;color:#555;line-height:14px}
.contact-row{display:flex;gap:10px;align-items:flex-start;margin-bottom:7px}
.foot-brand{left:761px;top:1097px;width:108px;text-align:center}
.foot-brand .mark{width:46px;height:46px;border-radius:50%;background:var(--green);margin:0 auto}
.copyright{left:690px;top:1153px;width:181px;text-align:right;font-size:9px;color:#555}
.social{left:752px;top:1172px;display:flex;gap:7px}
.social i{width:10px;height:10px;border-radius:50%;background:#555;display:block}
</style>
</head>
<body>

<header class="site-header abs">
  <div class="brand abs">
    <div class="brand-mark"></div>
    <div class="brand-name">Copperfleece</div>
  </div>
  <div class="utility abs">Members Resources &nbsp;|&nbsp; WebManager Login</div>
  <div class="search-box abs">Search
    <svg width="14" height="14" viewBox="0 0 14 14"><circle cx="6" cy="6" r="4.5" fill="none" stroke="#555" stroke-width="1.6"/><line x1="9.3" y1="9.3" x2="13" y2="13" stroke="#555" stroke-width="1.8"/></svg>
  </div>
  <div class="login-btn abs">Login</div>
</header>

<nav class="main-nav abs">
  <ul>
    <li class="active">Home</li><li>About</li><li>Search</li><li>Member Services</li><li>Stud Pages</li><li>News</li><li>Sales</li><li>Link</li><li>Contact Us</li>
  </ul>
</nav>

<section class="hero abs" role="img" aria-label="A flock of Copperfleece sheep standing on red earth in front of hills">
  <svg class="hero-arrow abs" style="left:107px" width="22" height="26" viewBox="0 0 22 26"><polyline points="18,2 4,13 18,24" fill="none" stroke="#fff" stroke-width="4"/></svg>
  <svg class="hero-arrow abs" style="left:849px" width="22" height="26" viewBox="0 0 22 26"><polyline points="4,2 18,13 4,24" fill="none" stroke="#fff" stroke-width="4"/></svg>
  <div class="hero-caption abs">The Copperfleece is proving to be the ideal prime lamb terminal sire<br>in wide-ranging areas and environments of Australia.</div>
</section>

<aside class="side-panel abs"></aside>
<div class="quick-btn abs" style="top:489px">
  <div class="ico"><svg width="28" height="28" viewBox="0 0 28 28"><circle cx="14" cy="14" r="12.5" fill="none" stroke="#fff" stroke-width="2"/><path d="M10 8c1-1 2 0 3 2s0 2-1 3c1 2 2 3 4 4 1-1 1-2 3-1s3 2 2 3c-2 2-5 2-8-1s-4-6-3-10z" fill="#fff"/></svg></div>
  <span>PRIME LAMB HELPLINE</span>
</div>
<div class="quick-btn abs" style="top:543px">
  <div class="ico"><svg width="26" height="28" viewBox="0 0 26 28"><rect x="2" y="5" width="22" height="21" rx="2" fill="none" stroke="#fff" stroke-width="2"/><line x1="2" y1="11" x2="24" y2="11" stroke="#fff" stroke-width="2"/><line x1="8" y1="2" x2="8" y2="7" stroke="#fff" stroke-width="2"/><line x1="18" y1="2" x2="18" y2="7" stroke="#fff" stroke-width="2"/><g fill="#fff"><rect x="6" y="14" width="3" height="3"/><rect x="11.5" y="14" width="3" height="3"/><rect x="17" y="14" width="3" height="3"/><rect x="6" y="19" width="3" height="3"/><rect x="11.5" y="19" width="3" height="3"/><rect x="17" y="19" width="3" height="3"/></g></svg></div>
  <span>UPCOMING EVENTS</span>
</div>
<div class="quick-btn abs" style="top:597px">
  <div class="ico"><svg width="30" height="28" viewBox="0 0 30 28"><circle cx="15" cy="6" r="4" fill="#fff"/><path d="M3 13l12 3 12-3v12l-12 3-12-3z" fill="none" stroke="#fff" stroke-width="2"/><line x1="15" y1="16" x2="15" y2="27" stroke="#fff" stroke-width="2"/></svg></div>
  <span>LATEST NEWS</span>
</div>

<div class="box-title ads-title abs">Members Advertisements
  <svg class="arrows" width="22" height="26" viewBox="0 0 22 26"><polyline points="7,8 2,13 7,18" fill="none" stroke="#fff" stroke-width="2.5"/><polyline points="15,8 20,13 15,18" fill="none" stroke="#fff" stroke-width="2.5"/></svg>
</div>
<div class="ad-slot abs" style="left:115px;background:linear-gradient(180deg,#e54a2a 0 18%,#8e9a72 18% 55%,#6a4a2e 55% 90%,#c8281e 90%)" role="img" aria-label="Livestock classifieds advertisement with cattle"></div>
<div class="ad-slot abs" style="left:238px;background:linear-gradient(180deg,#f1c9c9 0 28%,#d8a8a8 28% 80%,#f1c9c9 80%)" role="img" aria-label="Cattle stud semen sale advertisement with a bull"></div>

<section class="welcome abs">
  <h1>Welcome to <em>Copperfleece</em></h1>
  <p>Lorem ipsum dolor sit amet consectetur adipisicing elitsed do eiusmod tempor incididunt ut labore et dolo magna aliqua. Ut enim ad minim veniam, quis nostrud exercitation ullamco laboris nisi ut aliquip ex ecommo consequat. Duis aute irure dolor in reprehenderit in voluptate velit esse cillum dolore eu fugiat nulla pariatur. Excepteur sint occaecat cupidatat non proident, sunt in culpa qui officia deserunt mollit anim id est laborum. Duis aute irure dolor in reprehenderit in voluptate velit esse cillum dolore eu fugiat nulla pariatur. Excepteur sint occaecat cupidatat non proident, sunt in culpa qui officia deserunt mollit anim id est laborum. Sed ut perspiciatis unde omnis iste natus error sit voluptatem.</p>
</section>
<div class="read-more abs">Read more »</div>

<section class="semen card abs">
  <div class="box-title">Semen For Sale</div>
  <h3>From Registered Copperfleece<br>Stud Breeders</h3>
  <ul class="stud-list">
    <li><svg width="12" height="10" viewBox="0 0 12 10"><polyline points="1,5 4.5,9 11,1" fill="none" stroke="#0d9444" stroke-width="2.2"/></svg>Ashvale</li>
    <li><svg width="12" height="10" viewBox="0 0 12 10"><polyline points="1,5 4.5,9 11,1" fill="none" stroke="#0d9444" stroke-width="2.2"/></svg>Redgum Grove</li>
    <li><svg width="12" height="10" viewBox="0 0 12 10"><polyline points="1,5 4.5,9 11,1" fill="none" stroke="#0d9444" stroke-width="2.2"/></svg>Brightmoor</li>
    <li><svg width="12" height="10" viewBox="0 0 12 10"><polyline points="1,5 4.5,9 11,1" fill="none" stroke="#0d9444" stroke-width="2.2"/></svg>Larkspur</li>
    <li><svg width="12" height="10" viewBox="0 0 12 10"><polyline points="1,5 4.5,9 11,1" fill="none" stroke="#0d9444" stroke-width="2.2"/></svg>Clearwater</li>
    <li><svg width="12" height="10" viewBox="0 0 12 10"><polyline points="1,5 4.5,9 11,1" fill="none" stroke="#0d9444" stroke-width="2.2"/></svg>Hillcrest</li>
    <li><svg width="12" height="10" viewBox="0 0 12 10"><polyline points="1,5 4.5,9 11,1" fill="none" stroke="#0d9444" stroke-width="2.2"/></svg>Kendrick</li>
    <li><svg width="12" height="10" viewBox="0 0 12 10"><polyline points="1,5 4.5,9 11,1" fill="none" stroke="#0d9444" stroke-width="2.2"/></svg>Westmere</li>
  </ul>
</section>

<section class="calendar card abs">
  <div class="box-title">Sale Calendar</div>
  <table class="cal-table">
    <tr><th style="width:84px">Sale</th><th style="width:78px">Sale Start<br>Date</th><th>State</th></tr>
    <tr><td>Tallow Stud</td><td>01/01/2014</td><td>NSW/ACT</td></tr>
    <tr><td>Sorrento Park</td><td>10/10/2014</td><td>SA</td></tr>
    <tr><td>Ambleside</td><td>25/08/2014</td><td>SA</td></tr>
  </table>
  <div class="cal-more abs">More &gt;&gt;</div>
</section>

<section class="newsletter abs">
  <h2>Newsletter</h2>
  <div class="inner">
    <div class="email-field">Email address</div>
    <div class="subscribe">Subscribe</div>
  </div>
</section>

<section class="gallery card abs">
  <h2>Gallery</h2>
  <svg class="arrows" style="right:12px;top:11px" width="26" height="14" viewBox="0 0 26 14"><polyline points="8,2 3,7 8,12" fill="none" stroke="#444" stroke-width="2.5"/><polyline points="18,2 23,7 18,12" fill="none" stroke="#444" stroke-width="2.5"/></svg>
  <div class="thumb abs" style="left:12px"><div role="img" aria-label="Sheep in a paddock" style="background:linear-gradient(180deg,#4f4a40,#8c8578 60%,#3d3a33)"></div></div>
  <div class="sep abs" style="left:122px"></div>
  <div class="thumb abs" style="left:132px"><div role="img" aria-label="Sheep in a paddock" style="background:linear-gradient(180deg,#4f4a40,#8c8578 60%,#3d3a33)"></div></div>
  <div class="sep abs" style="left:242px"></div>
  <div class="thumb abs" style="left:252px"><div role="img" aria-label="Sheep on green grass" style="background:linear-gradient(180deg,#b8b8a8,#d8c4a6 55%,#6a9a4a)"></div></div>
  <div class="sep abs" style="left:362px"></div>
  <div class="thumb abs" style="left:372px"><div role="img" aria-label="Sheep on green grass" style="background:linear-gradient(180deg,#b8b8a8,#d8c4a6 55%,#6a9a4a)"></div></div>
</section>

<section class="sponsors abs">
  <h2>Our Sponsors</h2>
  <svg class="arrows" style="right:36px;top:12px" width="26" height="14" viewBox="0 0 26 14"><polyline points="8,2 3,7 8,12" fill="none" stroke="#444" stroke-width="2.5"/><polyline points="18,2 23,7 18,12" fill="none" stroke="#444" stroke-width="2.5"/></svg>
  <div class="rule"></div>
  <div class="sponsor" style="left:32px;color:#e02020">Northgate</div>
  <div class="sponsor" style="left:192px;color:#d42030">Vantera</div>
  <div class="sponsor" style="left:350px;color:#9c1020">Fieldcrest</div>
  <div class="sponsor" style="left:536px;color:#1f6aa0">Agrimax</div>
  <div class="sponsor" style="left:655px;color:#1d3f8c">Brolga</div>
</section>
<div class="sponsor-shadow abs"></div>

<footer class="site-footer abs"></footer>
<div class="foot-tag abs" style="left:108px">Quick Links</div>
<ul class="quick-links abs" style="left:108px">
  <li><svg width="5" height="8" viewBox="0 0 5 8"><polyline points="1,1 4,4 1,7" fill="none" stroke="#555" stroke-width="1.3"/></svg>Home</li>
  <li><svg width="5" height="8" viewBox="0 0 5 8"><polyline points="1,1 4,4 1,7" fill="none" stroke="#555" stroke-width="1.3"/></svg>About</li>
  <li><svg width="5" height="8" viewBox="0 0 5 8"><polyline points="1,1 4,4 1,7" fill="none" stroke="#555" stroke-width="1.3"/></svg>Search</li>
  <li><svg width="5" height="8" viewBox="0 0 5 8"><polyline points="1,1 4,4 1,7" fill="none" stroke="#555" stroke-width="1.3"/></svg>Member</li>
  <li><svg width="5" height="8" viewBox="0 0 5 8"><polyline points="1,1 4,4 1,7" fill="none" stroke="#555" stroke-width="1.3"/></svg>Services</li>
</ul>
<ul class="quick-links abs" style="left:177px">
  <li><svg width="5" height="8" viewBox="0 0 5 8"><polyline points="1,1 4,4 1,7" fill="none" stroke="#555" stroke-width="1.3"/></svg>Stud Pages</li>
  <li><svg width="5" height="8" viewBox="0 0 5 8"><polyline points="1,1 4,4 1,7" fill="none" stroke="#555" stroke-width="1.3"/></svg>News</li>
  <li><svg width="5" height="8" viewBox="0 0 5 8"><polyline points="1,1 4,4 1,7" fill="none" stroke="#555" stroke-width="1.3"/></svg>Sale</li>
  <li><svg width="5" height="8" viewBox="0 0 5 8"><polyline points="1,1 4,4 1,7" fill="none" stroke="#555" stroke-width="1.3"/></svg>Link</li>
  <li><svg width="5" height="8" viewBox="0 0 5 8"><polyline points="1,1 4,4 1,7" fill="none" stroke="#555" stroke-width="1.3"/></svg>Contact Us</li>
</ul>

<div class="map abs" role="img" aria-label="Street map showing the guild office location"></div>

<div class="foot-tag abs" style="left:508px">Contact Us</div>
<div class="contact-list abs">
  <div class="contact-row"><svg width="11" height="14" viewBox="0 0 11 14"><path d="M5.5 0a5 5 0 0 0-5 5c0 4 5 9 5 9s5-5 5-9a5 5 0 0 0-5-5z" fill="#555"/><circle cx="5.5" cy="5" r="1.8" fill="#fff"/></svg><div>PO Box 214,<br>Millbrook, SA 5092</div></div>
  <div class="contact-row"><svg width="11" height="12" viewBox="0 0 11 12"><path d="M2 1c1-1 2 0 3 2s0 2-1 3c1 2 2 3 3 3 1-1 1-2 3-1s2 2 1 3c-2 1-5 1-7-2S1 3 2 1z" fill="#555"/></svg><div>(08) 8000 4127</div></div>
  <div class="contact-row"><svg width="13" height="10" viewBox="0 0 13 10"><rect x="0.5" y="0.5" width="12" height="9" fill="#555"/><polyline points="1,1 6.5,5.5 12,1" fill="none" stroke="#fff" stroke-width="1"/></svg><div>info@copperfleece.org</div></div>
</div>

<div class="foot-brand abs"><div class="mark"></div></div>
<div class="copyright abs">© 2014 copperfleece. All Right Reserved.</div>
<div class="social abs"><i></i><i></i><i></i><i></i></div>

</body>
</html>
```